Local Flower Farm Needs Business Card Design

I need business cards designed for a flower farm based in Eudora, Kansas.
Business Info:
We are a local cut flower farm located in Eudora, Kansas, founded by Corinne Haldwick. What started as a passion for agriculture and search for more joy in daily life has blossomed into a small business dedicated to providing the community with beautiful, fresh, and sustainable flowers. We specialize in local, seasonal blooms, ensuring that every petal reflects the care and dedication we pour into our craft. Our mission is to deliver the highest quality flowers directly to our customers through local farmers markets and to florists who share our commitment to sustainability. Join us in celebrating the beauty of nature, one bloom at a time!
Contact Details:
Corinne Haldwick
Owner
Phone 913-555-0147
Facebook: Rosalind Thorpe Gardens
Instagram: @RosalindThorpeGardens
Website: RosalindThorpeGardens.example
Target Market(s)
Wholesale to Florists and Direct to Consumer via Farmers Market
Industry/Entity Type
Florist, Farm
Contact Information for Business Card
Name, Contact Info, Logo
Look and feel
Each slider illustrates characteristics of the customer's brand and the style your logo design should communicate.

```html
<!DOCTYPE html>
<html lang="en">
<head>
<meta charset="utf-8">
<title>Rosalind Thorpe Gardens – Business Cards</title>
<link rel="stylesheet" href="https://fonts.googleapis.com/css2?family=Libre+Baskerville:wght@400;700&display=swap">
<style>
  :root {
    --stage: #1c1e20;
    --teal-light: #0d3540;
    --teal-dark: #061c24;
    --ink: #0b2a33;
    --paper: #ffffff;
    --muted: #4a4f52;
    --line: #ffffff;
  }
  html, body {
    margin: 0;
    width: 1200px;
    height: 840px;
    overflow: hidden;
    background: var(--stage);
    font-family: "Libre Baskerville", "Times New Roman", serif;
  }
  .stage { position: relative; width: 1200px; height: 840px; }
  .card {
    position: absolute;
    width: 640px;
    height: 366px;
    border-radius: 28px;
    overflow: hidden;
    box-shadow: 0 18px 40px rgba(0,0,0,.45);
  }
  .card--front { left: 150px; top: 40px; background: linear-gradient(135deg, var(--teal-light), var(--teal-dark)); }
  .card--back { left: 410px; top: 434px; background: var(--paper); }
  .card svg { position: absolute; inset: 0; }

  .brand {
    position: absolute;
    margin: 0;
    text-align: center;
    color: var(--line);
    font-weight: 400;
    letter-spacing: .12em;
    text-transform: uppercase;
    line-height: 1.6;
    white-space: nowrap;
  }
  .card--front .brand { left: 0; right: 0; top: 157px; font-size: 16px; }
  .card--back .brand { left: 400px; width: 200px; top: 119px; font-size: 13px; }

  .holder { position: absolute; left: 44px; top: 118px; }
  .holder__name {
    margin: 0;
    font-size: 19px;
    font-weight: 700;
    letter-spacing: .02em;
    color: var(--ink);
    text-transform: uppercase;
    white-space: nowrap;
  }
  .holder__role { margin: 4px 0 0; font-size: 14px; color: var(--muted); }

  .contacts {
    position: absolute;
    left: 44px;
    bottom: 30px;
    margin: 0;
    padding: 0;
    list-style: none;
    font-size: 14.5px;
    color: var(--muted);
    white-space: nowrap;
  }
  .contacts li { display: flex; align-items: center; gap: 10px; height: 27px; }
  .contacts svg { position: static; width: 15px; height: 15px; flex: none; }
</style>
</head>
<body>
<main class="stage">

  <section class="card card--front" aria-label="Business card front">
    <svg width="640" height="366" viewBox="0 0 640 366" aria-hidden="true">
      <circle cx="320" cy="183" r="135" fill="none" stroke="var(--line)" stroke-width="1.5"/>
    </svg>
    <p class="brand">Rosalind Thorpe<br>Gardens</p>
  </section>

  <section class="card card--back" aria-label="Business card back">
    <svg width="640" height="366" viewBox="0 0 640 366" aria-hidden="true">
      <defs>
        <linearGradient id="disc" x1="0" y1="0" x2="1" y2="1">
          <stop offset="0" stop-color="var(--teal-dark)"/>
          <stop offset="1" stop-color="var(--teal-light)"/>
        </linearGradient>
      </defs>
      <circle cx="500" cy="140" r="185" fill="url(#disc)"/>
      <path d="M304 80 A205 205 0 0 0 423 330" fill="none" stroke="var(--ink)" stroke-width="1.6"/>
      <circle cx="304" cy="80" r="3.5" fill="var(--ink)"/>
      <circle cx="423" cy="330" r="3.5" fill="var(--ink)"/>
      <circle cx="500" cy="140" r="115" fill="none" stroke="var(--line)" stroke-width="1.4"/>
    </svg>
    <p class="brand">Rosalind Thorpe<br>Gardens</p>

    <div class="holder">
      <h1 class="holder__name">Corinne Haldwick</h1>
      <p class="holder__role">Owner</p>
    </div>

    <ul class="contacts">
      <li>
        <svg viewBox="0 0 16 16" aria-hidden="true"><path fill="var(--ink)" d="M3.6 1.5l2.2 2.6-1.3 1.6c.8 1.9 2.2 3.3 4.1 4.2l1.6-1.3 2.6 2.2-1.3 2.4C7 13.2 2.8 9 1.2 2.8z"/></svg>
        <span>913-555-0147</span>
      </li>
      <li>
        <svg viewBox="0 0 16 16" aria-hidden="true"><circle cx="8" cy="8" r="7" fill="var(--ink)"/></svg>
        <span>Rosalind Thorpe Gardens</span>
      </li>
      <li>
        <svg viewBox="0 0 16 16" aria-hidden="true"><circle cx="8" cy="8" r="7" fill="var(--ink)"/></svg>
        <span>@RosalindThorpeGardens</span>
      </li>
      <li>
        <svg viewBox="0 0 16 16" aria-hidden="true"><circle cx="8" cy="8" r="7" fill="var(--ink)"/><path d="M1 8h14M8 1c-3 3-3 11 0 14M8 1c3 3 3 11 0 14" fill="none" stroke="#fff" stroke-width="1"/></svg>
        <span>RosalindThorpeGardens.example</span>
      </li>
    </ul>
  </section>

</main>
</body>
</html>
```